Travel Agency Website - Simple General

Need a 7 page simple design that is pretty repetitive. Need to be able to load quickly that is SEO optimized. Trying to give ideas on what they can do, be personal as we are local, but at the same time come across as professional and get information easily with little burden.

- Landing Page
- Brimwell Vacations Page
- Family Trips
- Road Trips from Texas
- Other Destinations
- About Us Page
- Contact Us Page

Target Market(s)

Families

Coding

Coded - Design and coding required

Number of Pages Required

5+ page

Colors

Designer to choose colors to be used in the design.

Requirements
Must have
• Like it to flow easily with our logo. Use that for colors, etc.

```html
<!DOCTYPE html>
<html lang="en">
<head>
<meta charset="utf-8">
<title>Lantern Trail Travel Co. – Page Designs</title>
<link href="https://fonts.googleapis.com/css2?family=Poppins:wght@300;400;500;600;800&display=swap" rel="stylesheet">
<style>
:root{
  --board:#d3d3d3;
  --cream:#faf7ee;
  --teal:#2d6f73;
  --teal-soft:#cfe0dc;
  --ink:#1b1b1b;
  --footer:#123238;
  --gold:#b8974a;
  --white:#ffffff;
  --field:#f3f0e6;
  --line:#d9d3c2;
}
*{margin:0;padding:0;box-sizing:border-box}
html,body{width:1200px;height:1052px;overflow:hidden;background:var(--board);font-family:'Poppins',sans-serif;color:var(--ink)}
.board{position:relative;width:1200px;height:1052px}
.page{position:absolute;width:554px;height:312px;background:var(--cream);overflow:hidden}
.p-home{left:29px;top:29px}
.p-road{left:611px;top:29px}
.p-brim{left:29px;top:370px}
.p-other{left:611px;top:370px}
.p-family{left:29px;top:711px}

.site-header{position:absolute;left:0;top:0;width:100%;height:26px;background:var(--cream);z-index:3}
.brand{position:absolute;left:42px;top:7px;display:flex;align-items:center;gap:3px;z-index:4}
.brand-dot{width:12px;height:12px;border-radius:50%;background:var(--teal-soft);border:1px solid var(--teal)}
.brand-name{font-size:6.5px;font-weight:600;color:var(--teal);line-height:1}
.nav{position:absolute;right:40px;top:9px;display:flex;gap:9.4px;font-size:5.6px;letter-spacing:.1px;color:var(--ink)}
.nav .active{color:var(--teal);border-bottom:0.7px solid var(--teal);padding-bottom:1px}
.p-home .site-header{height:80px;background:transparent}
.p-home .nav{top:17px}
.p-home .brand{top:14px}

.hero{position:absolute;left:0;top:26px;width:100%;height:258px}
.hero-shade{position:absolute;inset:0;background:linear-gradient(180deg,rgba(0,0,0,.15) 0%,rgba(0,0,0,.3) 55%,rgba(0,0,0,.75) 100%)}
.photo-road{background:linear-gradient(120deg,#3c3a36 0%,#8a7a66 35%,#c9c2b6 60%,#6f7d8a 100%)}
.photo-brim{background:linear-gradient(180deg,#6d9aa0 0%,#7fa6a8 25%,#3f6b4a 45%,#2f7c85 62%,#1d3b38 100%)}
.photo-other{background:linear-gradient(180deg,#9fb4ba 0%,#c7c3b6 25%,#6f7b78 45%,#35443f 70%,#101a17 100%)}
.photo-family{background:linear-gradient(110deg,#6b6560 0%,#b9ad9c 30%,#d8cdbd 45%,#6e5e4c 70%,#1c1c1c 100%)}

.hero-copy{position:absolute;left:0;right:0;top:104px;text-align:center;color:var(--white)}
.tagline{font-weight:400;font-size:13px;letter-spacing:2.5px;line-height:1.2;text-transform:uppercase}
.title{font-weight:800;font-size:26px;line-height:1.05;letter-spacing:-.2px;margin-top:4px}
.lede{font-size:5.3px;margin-top:5px}
.btn{display:inline-block;margin-top:8px;background:var(--gold);color:var(--white);font-size:6.8px;font-weight:500;padding:5px 9px;letter-spacing:.2px}

.form-card{position:absolute;left:76px;top:218px;width:403px;height:49px;background:var(--cream);padding:5px 6px;z-index:2}
.form-kicker{font-size:4.8px;font-weight:600;color:var(--teal);height:8px}
.form-kicker .off{color:var(--ink);font-weight:400;margin-left:5px}
.form-kicker .dot{display:inline-block;width:3px;height:3px;border-radius:50%;background:var(--teal);margin-right:2px;vertical-align:middle}
.form-kicker .ring{display:inline-block;width:3px;height:3px;border-radius:50%;border:0.5px solid #777;margin-right:2px;vertical-align:middle}
.fields{display:flex;gap:3px;margin-top:3px;align-items:flex-end}
.field{flex:1}
.field label{display:block;font-size:4.8px;font-weight:500;margin-bottom:2px}
.field span{display:block;height:14px;border:0.6px solid var(--line);background:var(--field);position:relative}
.field span::after{content:"";position:absolute;right:4px;top:5px;width:3px;height:3px;border-radius:50%;background:#888}
.submit{width:52px;height:14px;background:var(--gold);color:var(--white);font-size:6.5px;font-weight:500;display:flex;align-items:center;justify-content:center}
.p-brim .form-card{left:47px;width:461px}

.site-footer{position:absolute;left:0;top:296px;width:100%;height:16px;background:var(--footer);color:var(--white);font-size:5px;display:flex;align-items:center;padding:0 42px;justify-content:space-between}
.social{display:flex;gap:5px}
.social i{width:9px;height:9px;border-radius:50%;border:0.7px solid var(--white);display:block}

.home-backdrop{position:absolute;inset:0;background:linear-gradient(180deg,var(--cream) 0%,#eef2ea 40%,#dfe9e3 70%,var(--cream) 100%)}
.home-copy{position:absolute;left:0;right:0;top:80px;text-align:center}
.home-copy .tagline{color:var(--teal)}
.home-copy .title{color:var(--ink);font-size:27px}
.home-copy .lede{color:var(--ink);margin-top:6px}
.tile{position:absolute;width:115px;height:64px;top:215px;color:var(--white);font-size:7px;font-weight:500}
.tile-img{position:absolute;inset:0}
.tile-name{position:absolute;left:4px;bottom:5px}
.tile-arrow{position:absolute;right:4px;bottom:4px;width:9px;height:9px;background:var(--gold);display:flex;align-items:center;justify-content:center}
.tile-arrow svg{width:5px;height:5px}
.tile.tall{top:173px;height:106px}
.tile.tall .tile-name{bottom:26px}
.tile-blurb{position:absolute;left:4px;right:16px;bottom:5px;font-size:3.8px;font-weight:400;line-height:1.3}
.tile.tall .tile-arrow{background:var(--white)}
</style>
</head>
<body>
<main class="board">

<!-- Landing -->
<section class="page p-home">
  <div class="home-backdrop" role="img" aria-label="Soft misty teal mountain range backdrop"></div>
  <header class="site-header">
    <div class="brand"><i class="brand-dot"></i><span class="brand-name">Lantern Trail Travel Co.</span></div>
    <nav class="nav"><span>HOME</span><span>BRIMWELL VACATIONS</span><span>FAMILY TRIPS</span><span>TEXAS ROAD TRIPS</span><span>OTHER DESTINATIONS</span><span>ABOUT US</span><span>CONTACT US</span></nav>
  </header>
  <div class="home-copy">
    <div class="tagline">Lantern Trail Travel Co.</div>
    <h1 class="title">ADVENTURE STARTS WITH ONE TRIP</h1>
    <p class="lede">Helping families create stress-free Brimwell vacations, cruises, road trips, and unforgettable travel experiences tailored to every adventure.</p>
  </div>
  <a class="tile" style="left:42px"><div class="tile-img photo-brim" role="img" aria-label="Green island hill above a turquoise sea"></div><span class="tile-name">Brimwell Vacations</span><span class="tile-arrow"><svg viewBox="0 0 10 10"><path d="M3 1l4 4-4 4" fill="none" stroke="#fff" stroke-width="1.6"/></svg></span></a>
  <a class="tile tall" style="left:160px"><div class="tile-img photo-family" role="img" aria-label="Family running together with a kite beside a car"></div><span class="tile-name">Family Trips</span><span class="tile-blurb">Thoughtfully planned family getaways designed to create fun, connection, and unforgettable memories for every age.</span><span class="tile-arrow"><svg viewBox="0 0 10 10"><path d="M3 1l4 4-4 4" fill="none" stroke="#333" stroke-width="1.6"/></svg></span></a>
  <a class="tile" style="left:279px"><div class="tile-img photo-road" role="img" aria-label="Travellers planning a trip around a table with a globe"></div><span class="tile-name">Texas Road Trips</span><span class="tile-arrow"><svg viewBox="0 0 10 10"><path d="M3 1l4 4-4 4" fill="none" stroke="#fff" stroke-width="1.6"/></svg></span></a>
  <a class="tile" style="left:398px"><div class="tile-img photo-other" role="img" aria-label="Rugged snowy mountain peaks"></div><span class="tile-name">Other Destinations</span><span class="tile-arrow"><svg viewBox="0 0 10 10"><path d="M3 1l4 4-4 4" fill="none" stroke="#fff" stroke-width="1.6"/></svg></span></a>
  <footer class="site-footer"><span>© 2026 Lantern Trail Travel Co. All Rights Reserved.</span><span class="social"><i></i><i></i></span></footer>
</section>

<!-- Road trips -->
<section class="page p-road">
  <header class="site-header">
    <div class="brand"><i class="brand-dot"></i><span class="brand-name">Lantern Trail Travel Co.</span></div>
    <nav class="nav"><span>HOME</span><span>BRIMWELL VACATIONS</span><span>FAMILY TRIPS</span><span class="active">TEXAS ROAD TRIPS</span><span>OTHER DESTINATIONS</span><span>ABOUT US</span><span>CONTACT US</span></nav>
  </header>
  <div class="hero photo-road" role="img" aria-label="Three travellers planning a road trip at a table"><div class="hero-shade"></div></div>
  <div class="hero-copy">
    <div class="tagline">Lantern Trail Travel Co.</div>
    <h1 class="title">ROAD TRIPS FROM TEXAS</h1>
    <p class="lede">Explore scenic Texas road trips with flexible travel plans, family-friendly adventures, and optional van rentals for the perfect getaway.</p>
    <span class="btn">PLAN YOUR FAMILY TRIP</span>
  </div>
  <form class="form-card">
    <div class="form-kicker">ROAD TRIP</div>
    <div class="fields">
      <div class="field"><label>DESTINATION</label><span></span></div>
      <div class="field"><label>START DATE</label><span></span></div>
      <div class="field"><label>END DATE</label><span></span></div>
      <div class="field"><label>PEOPLE</label><span></span></div>
      <div class="field"><label>VAN RENTAL</label><span></span></div>
      <div class="submit">SUBMIT</div>
    </div>
  </form>
  <footer class="site-footer"><span>© 2026 Lantern Trail Travel Co. All Rights Reserved.</span><span class="social"><i></i><i></i></span></footer>
</section>

<!-- Brimwell vacations -->
<section class="page p-brim">
  <header class="site-header">
    <div class="brand"><i class="brand-dot"></i><span class="brand-name">Lantern Trail Travel Co.</span></div>
    <nav class="nav"><span>HOME</span><span class="active">BRIMWELL VACATIONS</span><span>FAMILY TRIPS</span><span>TEXAS ROAD TRIPS</span><span>OTHER DESTINATIONS</span><span>ABOUT US</span><span>CONTACT US</span></nav>
  </header>
  <div class="hero photo-brim" role="img" aria-label="Green coastal hill over a turquoise sea"><div class="hero-shade"></div></div>
  <div class="hero-copy">
    <div class="tagline">Lantern Trail Travel Co.</div>
    <h1 class="title">BRIMWELL VACATIONS</h1>
    <p class="lede">Magical Brimwell park vacations and unforgettable cruise experiences designed for the whole family.</p>
    <span class="btn">PLAN YOUR BRIMWELL TRIP</span>
  </div>
  <form class="form-card">
    <div class="form-kicker"><i class="dot"></i>BRIMWELL WORLD <span class="off"><i class="ring"></i>BRIMWELL CRUISE</span></div>
    <div class="fields">
      <div class="field"><label>PEOPLE</label><span></span></div>
      <div class="field"><label>START DATE</label><span></span></div>
      <div class="field"><label>END DATE</label><span></span></div>
      <div class="field"><label>PARK</label><span></span></div>
      <div class="field"><label>RESOTS</label><span></span></div>
      <div class="field"><label>EXPERIENCE</label><span></span></div>
      <div class="submit">SUBMIT</div>
    </div>
  </form>
  <footer class="site-footer"><span>© 2026 Lantern Trail Travel Co. All Rights Reserved.</span><span class="social"><i></i><i></i></span></footer>
</section>

<!-- Other destinations -->
<section class="page p-other">
  <header class="site-header">
    <div class="brand"><i class="brand-dot"></i><span class="brand-name">Lantern Trail Travel Co.</span></div>
    <nav class="nav"><span>HOME</span><span>BRIMWELL VACATIONS</span><span>FAMILY TRIPS</span><span>TEXAS ROAD TRIPS</span><span class="active">OTHER DESTINATIONS</span><span>ABOUT US</span><span>CONTACT US</span></nav>
  </header>
  <div class="hero photo-other" role="img" aria-label="Snowy mountain range above a dark forested valley"><div class="hero-shade"></div></div>
  <div class="hero-copy">
    <div class="tagline">Lantern Trail Travel Co.</div>
    <h1 class="title">OTHER DESTINATIONS</h1>
    <p class="lede">Discover custom travel experiences tailored to your dream destination and travel style.</p>
    <span class="btn">PLAN OTHER DESTINATION</span>
  </div>
  <form class="form-card">
    <div class="form-kicker">OTHER DESTINATIONS</div>
    <div class="fields">
      <div class="field"><label>DESTINATION</label><span></span></div>
      <div class="field"><label>START DATE</label><span></span></div>
      <div class="field"><label>END DATE</label><span></span></div>
      <div class="field"><label>PEOPLE</label><span></span></div>
      <div class="field"><label>EXPERIENCE</label><span></span></div>
      <div class="submit">SUBMIT</div>
    </div>
  </form>
  <footer class="site-footer"><span>© 2026 Lantern Trail Travel Co. All Rights Reserved.</span><span class="social"><i></i><i></i></span></footer>
</section>

<!-- Family trips -->
<section class="page p-family">
  <header class="site-header">
    <div class="brand"><i class="brand-dot"></i><span class="brand-name">Lantern Trail Travel Co.</span></div>
    <nav class="nav"><span>HOME</span><span>BRIMWELL VACATIONS</span><span class="active">FAMILY TRIPS</span><span>TEXAS ROAD TRIPS</span><span>OTHER DESTINATIONS</span><span>ABOUT US</span><span>CONTACT US</span></nav>
  </header>
  <div class="hero photo-family" role="img" aria-label="Family running with a kite at sunset beside an open car"><div class="hero-shade"></div></div>
  <div class="hero-copy">
    <div class="tagline">Lantern Trail Travel Co.</div>
    <h1 class="title">FAMILY TRIPS</h1>
    <p class="lede">Family adventures designed for fun, connection, and lasting memories.</p>
    <span class="btn">PLAN YOUR FAMILY TRIP</span>
  </div>
  <form class="form-card">
    <div class="form-kicker">FAMILY TRIP</div>
    <div class="fields">
      <div class="field"><label>DESTINATION</label><span></span></div>
      <div class="field"><label>START DATE</label><span></span></div>
      <div class="field"><label>END DATE</label><span></span></div>
      <div class="field"><label>PEOPLE</label><span></span></div>
      <div class="field"><label>EXPERIENCE</label><span></span></div>
      <div class="submit">SUBMIT</div>
    </div>
  </form>
  <footer class="site-footer"><span>© 2026 Lantern Trail Travel Co. All Rights Reserved.</span><span class="social"><i></i><i></i></span></footer>
</section>

</main>
</body>
</html>
```